Business card for law firm

Need business card for new law firm. Think confident, authoritative, conservative, but not stuffy or old-fashioned.

Contact Information for Business Card

Content for card - logo (uploaded), plus the following:

Paul Whitcombe (larger font)
Managing Partner (larger font, but not as large as name)
Level 9, 7 Ferris Lane
Sydney NSW 2000
Main Tel 02 9364 2710
Direct Tel 02 8472 3159
Email paul@qvlegal.com.au
www.qvlegal.com.au

Letterhead design should include logo plus:
Level 9, 7 Ferris Lane
Sydney NSW 2000
Tel 02 8472 3159
www.qvlegal.com.au

```html
<!DOCTYPE html>
<html lang="en">
<head>
<meta charset="utf-8">
<title>Quayvale Legal — Business Card</title>
<link href="https://fonts.googleapis.com/css2?family=Cinzel:wght@600&family=Open+Sans:wght@400;600&display=swap" rel="stylesheet">
<style>
  :root {
    --backdrop: #3a3b3e;
    --navy: #0d2463;
    --navy-deep: #081a4d;
    --card-light: #e6e6e7;
    --card-shade: #d6d6d8;
    --ink: #1b1d24;
    --text-grey: #3c3d42;
    --rule: #b9babd;
    --back-text: #d9dbe2;
  }
  * { box-sizing: border-box; margin: 0; padding: 0; }
  html, body { width: 1200px; height: 896px; overflow: hidden; }
  body {
    background: var(--backdrop);
    display: flex;
    flex-direction: column;
    align-items: center;
    justify-content: center;
    gap: 56px;
    font-family: "Open Sans", Arial, sans-serif;
  }
  .card {
    position: relative;
    width: 540px;
    height: 330px;
    box-shadow: 0 14px 30px rgba(0,0,0,.45);
    overflow: hidden;
  }
  /* Front */
  .card-front {
    background: linear-gradient(90deg, var(--card-shade) 0%, var(--card-light) 45%, var(--card-light) 100%);
    border-bottom: 9px solid var(--navy);
  }
  .contact-block {
    position: absolute;
    left: 34px;
    top: 56px;
    width: 236px;
  }
  .person-name {
    font-family: "Cinzel", Georgia, serif;
    font-weight: 600;
    font-size: 20px;
    color: var(--navy);
    letter-spacing: .5px;
    line-height: 1.1;
  }
  .person-role {
    font-size: 15px;
    color: var(--text-grey);
    margin-top: 2px;
  }
  .contact-list {
    list-style: none;
    margin-top: 8px;
    padding-top: 8px;
    border-top: 1px solid var(--rule);
  }
  .contact-list li {
    display: flex;
    align-items: center;
    gap: 8px;
    font-size: 13.5px;
    color: var(--text-grey);
    line-height: 1.55;
    white-space: nowrap;
  }
  .contact-list svg { width: 12px; height: 12px; fill: var(--navy); flex: none; }
  .firm-mark {
    position: absolute;
    right: 40px;
    top: 124px;
    display: flex;
    align-items: center;
    gap: 10px;
  }
  .mark-square {
    width: 18px;
    height: 18px;
    background: var(--navy);
  }
  .firm-name {
    font-family: "Open Sans", Arial, sans-serif;
    font-weight: 600;
    font-size: 24px;
    color: var(--navy);
    line-height: 1;
    white-space: nowrap;
  }
  .address {
    position: absolute;
    right: 40px;
    bottom: 30px;
    width: 230px;
    padding-top: 10px;
    border-top: 1px solid var(--rule);
    text-align: right;
    font-size: 14px;
    font-style: normal;
    color: var(--text-grey);
    line-height: 1.45;
  }
  /* Back */
  .card-back {
    background: radial-gradient(ellipse at 30% 30%, var(--navy) 0%, var(--navy-deep) 100%);
    display: flex;
    align-items: center;
    justify-content: center;
  }
  .card-back .firm-name { color: var(--back-text); font-size: 36px; }
</style>
</head>
<body>

<section class="card card-front" aria-label="Business card front">
  <div class="contact-block">
    <h1 class="person-name">PAUL WHITCOMBE</h1>
    <p class="person-role">Managing Partner</p>
    <ul class="contact-list">
      <li><svg viewBox="0 0 12 12" aria-hidden="true"><path d="M1 4c0-2 2-3 5-3s5 1 5 3v1H8V4H4v1H1zM3 6h6l1.5 5h-9z"/></svg>02 9364 2710</li>
      <li><svg viewBox="0 0 12 12" aria-hidden="true"><path d="M1 4c0-2 2-3 5-3s5 1 5 3v1H8V4H4v1H1zM3 6h6l1.5 5h-9z"/></svg>02 8472 3159 (DIRECT)</li>
      <li><svg viewBox="0 0 12 12" aria-hidden="true"><path d="M0 2h12v8H0zM1 3l5 4 5-4v-.2H1z" fill-rule="evenodd"/></svg>paul@qvlegal.com.au</li>
      <li><svg viewBox="0 0 12 12" aria-hidden="true"><circle cx="6" cy="6" r="5.5"/></svg>www.qvlegal.com.au</li>
    </ul>
  </div>

  <div class="firm-mark">
    <span class="mark-square" aria-hidden="true"></span>
    <p class="firm-name">Quayvale Legal</p>
  </div>

  <address class="address">
    Level 9, 7 Ferris Lane<br>
    Sydney NSW 2000
  </address>
</section>

<section class="card card-back" aria-label="Business card back">
  <p class="firm-name">Quayvale Legal</p>
</section>

</body>
</html>
```